Computer consultant business card

Bexil Software is a newly started computer consulting company. It's a small one-man company that provides mostly Vornix applications but also websites in collaboration with designers. I'm running this company on the side of full time university studies.

I want the final design to be clean and memorable. Be creative! :)

Some inspiration:
http://www.pixelmarta.com/design/48317
http://www.pixelmarta.com/design/2739164/business-card-design-by-frostlynk
http://www.pixelmarta.com/design/604281/business-card-design-by-koralind-vestrabanu

See attachment for my company logo.
Updates

I would like to thank everyone for submitting! I'll need a couple of days to review and ultimately select a design.

Target Market(s)

Non-technical entrepreneurs and small companies.

Industry/Entity Type

University

Requirements
Must have
• My company logo.
In any way, both colors from my logo.
First- and last name, e-mail and phone number.
Double-sided design.
Nice to have
• Something creative with the symbol in my logo

```html
<!DOCTYPE html>
<html lang="en">
<head>
<meta charset="utf-8">
<title>Bexil Software – Business Card</title>
<link rel="stylesheet" href="https://fonts.googleapis.com/css2?family=Maven+Pro:wght@400;500&display=swap">
<style>
  :root {
    --stage: #e4e7ea;
    --card-white: #ffffff;
    --ink-dark: #3b3b3d;
    --brand-blue: #2a7de1;
    --back-blue-deep: #2b63c0;
    --back-blue-light: #1c9fd8;
    --shadow: rgba(20, 40, 60, 0.18);
  }
  * { box-sizing: border-box; margin: 0; padding: 0; }
  html, body {
    width: 1200px;
    height: 960px;
    overflow: hidden;
    background: var(--stage);
    font-family: "Maven Pro", sans-serif;
  }
  .canvas {
    width: 1200px;
    height: 960px;
    display: flex;
    flex-direction: column;
    align-items: center;
    justify-content: center;
    gap: 40px;
  }
  .card {
    position: relative;
    width: 700px;
    height: 400px;
    border-radius: 4px;
    box-shadow: 0 10px 30px var(--shadow);
    overflow: hidden;
  }

  /* Front side */
  .card-front { background: var(--card-white); }
  .brand {
    position: absolute;
    left: 46px;
    top: 58px;
    display: flex;
    align-items: center;
    gap: 22px;
  }
  .brand-dot {
    width: 64px;
    height: 64px;
    border-radius: 50%;
    background: var(--brand-blue);
  }
  .brand-name {
    font-size: 72px;
    font-weight: 500;
    color: var(--ink-dark);
    line-height: 1;
    letter-spacing: 1px;
  }
  .holder-name {
    position: absolute;
    left: 48px;
    top: 238px;
    font-size: 30px;
    font-weight: 400;
    letter-spacing: 1.5px;
    color: var(--ink-dark);
    text-transform: uppercase;
  }
  .contact-list {
    position: absolute;
    left: 48px;
    top: 306px;
    list-style: none;
    font-size: 19px;
    line-height: 1.3;
    color: var(--ink-dark);
  }
  .contact-label {
    display: inline-block;
    width: 22px;
    color: var(--brand-blue);
  }

  /* Back side */
  .card-back {
    background: linear-gradient(135deg, var(--back-blue-deep) 0%, var(--back-blue-light) 60%, var(--back-blue-deep) 100%);
  }
  .back-brand {
    position: absolute;
    left: 50%;
    top: 50%;
    transform: translate(-50%, -50%);
    display: flex;
    align-items: center;
    gap: 22px;
  }
  .back-brand .brand-dot { background: var(--card-white); }
  .back-brand .brand-name { color: var(--card-white); }
</style>
</head>
<body>
  <main class="canvas">
    <section class="card card-front" aria-label="Business card front">
      <div class="brand">
        <span class="brand-dot"></span>
        <span class="brand-name">bexil</span>
      </div>
      <p class="holder-name">Mara Kellin</p>
      <ul class="contact-list">
        <li><span class="contact-label">t</span>555.014.2271</li>
        <li><span class="contact-label">e</span>mara_kellin@bexilmail.com</li>
      </ul>
    </section>

    <section class="card card-back" aria-label="Business card back">
      <div class="back-brand">
        <span class="brand-dot"></span>
        <span class="brand-name">bexil</span>
      </div>
    </section>
  </main>
</body>
</html>
```